KAJU Freightways #ALLKAJU Business Cards & Letterhead

I am looking to business cards designed for our organization. We are currently undergoing a small re-branding that is taking place. Our organization is called KAJU Freightways and we are headquartered in Phoenix, AZ. We primarily provide transportation and logistics services to the Marlow Parcel Bureau who is our largest customer. I would like to see a design that incorporates name, title, contact info, website, and address (this will be different depending on the employee). I would also like to see some color on the business card using our logo colors or a variation. I would like our logo on the back of the business card with the website displayed. The final design should communicate that we are a next generation transportation operate that focuses on being driver-first, customer-centric, innovative, and sustainable.We would also like our #ALLKAJU catch phrase incorporated as well.

Target Market(s)

Transportation & Logistics

Industry/Entity Type

Trucking Company

Contact Information for Business Card

-First and Last Name
-Position Title
-Contact Phone
-Contact Email
-Physical Address

Font styles to use
Serif

Colors

Designer to choose colors to be used in the design.

Requirements
Must have
• -KAJU logo prominently displayed
• -#ALLKAJU catch phrase used
• -Some amount of color, design gradient, etc.
• -Logo on the back with website listed (https://www.kajufreightco.example)

```html
<!DOCTYPE html>
<html lang="en">
<head>
<meta charset="utf-8">
<title>KAJU Freightways Business Card</title>
<link href="https://fonts.googleapis.com/css2?family=Roboto+Slab:wght@400;500;700&display=swap" rel="stylesheet">
<style>
  :root {
    --backdrop: #bdbdbd;
    --lime: #7ab929;
    --green-mid: #4e9a3a;
    --teal-dark: #0b3a44;
    --card-white: #f1f1f0;
    --ink: #1f2f36;
  }
  * { box-sizing: border-box; margin: 0; padding: 0; }
  html, body { width: 1200px; height: 576px; overflow: hidden; }
  body {
    background: var(--backdrop);
    font-family: "Roboto Slab", Georgia, serif;
    position: relative;
  }
  .card {
    position: absolute;
    top: 138px;
    height: 294px;
    border-radius: 10px;
    overflow: hidden;
    box-shadow: 0 3px 8px rgba(0,0,0,.25);
  }
  /* Back */
  .card-back { left: 82px; width: 484px; }
  .card-back .photo-area {
    position: absolute; inset: 0;
    background: linear-gradient(120deg, var(--lime) 0%, var(--green-mid) 30%, #2f6b4f 60%, var(--teal-dark) 100%);
  }
  .logo-ring {
    position: absolute;
    border-radius: 50%;
    display: flex; align-items: center; justify-content: center;
  }
  .card-back .logo-ring {
    left: 163px; top: 60px; width: 156px; height: 156px;
    border: 5px solid #fff;
  }
  .logo-name {
    font-family: "Roboto Slab", Georgia, serif;
    font-weight: 700;
    letter-spacing: 1px;
  }
  .card-back .logo-name { color: #fff; font-size: 40px; }
  .back-web {
    position: absolute; left: 0; right: 0; top: 262px;
    display: flex; align-items: center; justify-content: center; gap: 14px;
    color: #e8efe8; font-size: 12.5px; letter-spacing: 2.2px;
  }
  .back-web .rule { width: 30px; height: 2px; background: var(--lime); }

  /* Front */
  .card-front { left: 602px; width: 481px; background: var(--card-white); }
  .wave { position: absolute; inset: 0; }
  .holder { position: absolute; left: 22px; top: 20px; color: #fff; }
  .holder .name { font-weight: 700; font-size: 20px; }
  .holder .title { font-size: 12px; margin-top: 4px; color: #e3eaec; }
  .details { position: absolute; left: 22px; top: 142px; color: var(--ink); font-size: 12.5px; }
  .details .service { color: var(--lime); font-weight: 700; font-size: 12.5px; margin-bottom: 11px; }
  .details .address { line-height: 18.5px; margin-bottom: 14px; }
  .contact { list-style: none; line-height: 18.5px; }
  .contact li { display: flex; align-items: center; gap: 12px; }
  .contact svg { width: 11px; height: 11px; fill: var(--lime); flex: none; }
  .card-front .logo-ring {
    left: 285px; top: 100px; width: 156px; height: 156px;
    border: 4px solid var(--lime);
  }
  .card-front .logo-name { color: var(--teal-dark); font-size: 40px; }
  .catch-phrase {
    position: absolute; left: 285px; width: 156px; top: 264px;
    text-align: center; color: var(--lime);
    font-weight: 700; font-size: 12.5px; letter-spacing: 1.5px;
  }
</style>
</head>
<body>
  <section class="card card-back">
    <div class="photo-area" role="img" aria-label="Photo of a semi-truck tractor under a green to teal tint"></div>
    <div class="logo-ring"><span class="logo-name">KAJU</span></div>
    <div class="back-web"><span class="rule"></span><span>www.kajufreightco.example</span><span class="rule"></span></div>
  </section>

  <section class="card card-front">
    <svg class="wave" viewBox="0 0 481 294" preserveAspectRatio="none" aria-hidden="true">
      <path d="M0 0 H481 V58 C420 50 360 56 300 80 C230 110 150 110 80 104 C45 101 20 98 0 100 Z" fill="#0b3a44"/>
      <path d="M0 100 C20 98 45 101 80 104 C150 110 230 110 300 80 C360 56 420 50 481 58 V64 C420 58 360 64 300 88 C230 118 150 120 80 114 C45 111 20 110 0 114 Z" fill="#fff"/>
      <path d="M0 112 C30 108 60 112 90 115 C160 122 235 120 305 90 C365 64 425 60 481 66 V76 C425 70 365 76 305 100 C235 130 160 132 90 126 C60 123 30 122 0 124 Z" fill="#7ab929"/>
      <path d="M240 40 C300 10 380 4 481 26 V34 C390 18 310 22 240 40 Z" fill="#7ab929"/>
      <path d="M280 40 C340 24 400 22 440 32 C400 28 340 32 280 40 Z" fill="#7ab929"/>
    </svg>
    <div class="holder">
      <div class="name">Dana Whitlock</div>
      <div class="title">Chairman &amp; CEO</div>
    </div>
    <div class="details">
      <div class="service">Transportation &amp; Energy Services</div>
      <div class="address">4120 North Canyon Ridge<br>Parkway Glendale, AZ 85310</div>
      <ul class="contact">
        <li><svg viewBox="0 0 12 12"><path d="M2.5 1 L4.5 1 L5.2 3.6 L4 4.6 C4.7 6 6 7.3 7.4 8 L8.4 6.8 L11 7.5 V9.5 C11 10.3 10.3 11 9.5 11 C5 11 1 7 1 2.5 C1 1.7 1.7 1 2.5 1Z"/></svg>623-555-0148</li>
        <li><svg viewBox="0 0 12 12"><path d="M0 2 H12 V10 H0 Z M0.8 2.6 L6 6.8 L11.2 2.6 V3.4 L6 7.6 L0.8 3.4 Z" fill-rule="evenodd"/></svg>dana@kajufreightco.example</li>
        <li><svg viewBox="0 0 12 12"><circle cx="6" cy="6" r="5.5"/><path d="M0.5 6 H11.5 M6 0.5 C3.5 3 3.5 9 6 11.5 M6 0.5 C8.5 3 8.5 9 6 11.5" stroke="#f1f1f0" stroke-width="0.9" fill="none"/></svg>www.kajufreightco.example</li>
      </ul>
    </div>
    <div class="logo-ring"><span class="logo-name">KAJU</span></div>
    <div class="catch-phrase">#ALLKAJU</div>
  </section>
</body>
</html>
```